Wordpress Web Design & Coding for velcorahealth.ca

We need a website for a new investment company that is visually grabbing and vibrant. We would like to see a web page that displays trust, growth and confidence. Needs to be responsive and mobile friendly for all browsers and coded for both Android & IOS.

Open to the number of pages and menu items. I selected 4 but if you feel the layout would work better with less I am open to this. Need to sell the people (management team/related businesses) and then show where the invested money will be going (upcoming projects).

Company Info:

Vel Cora is an investment company put together by a group of seasoned business professionals who have come together to combine decades of success in the real estate development, management, financing and medical services. The company will be a full service company offering turn key solutions for medical professionals.

Vel-Cora will focus on providing a full range of services via a group of distinct companies to deliver newly emerging needs of the medical community. The end goal will be to create complete solutions for individuals in the medical community. Our group has experience and success with the conceptualization, construction and financing of medical and dental clinic spaces. Vel-Cora Solutions will be established to accommodate all areas of the development and creation of clinics for medical professionals from building construction to equipment financing and administrations.

You can mention these companies and take photos from their websites. You can also use stock photos.

Our construction partner:
https://318bld.com/projects/

Our equipment leasing partner:
https://www.norvixa.com/

Our Management Team and medical partners

Gil Parish
https://www.ourfirmstance.ca/

Dietmar Vellasquin
https://www.gshdentalservices.com/about-us

PROPOSED PROJECTS (see attachment for details)
Pinegrove Business Park
Holtmere Business Park
Mt. Corwin Ridge Professional

Target Market(s)

Investors

Industry/Entity Type

Investment

Coding

Coded - Design and coding required

Number of Pages Required

4 page

Font styles to use
Sans Serif

Requirements
Must have
• Wordpress – must be both desktop and mobile friendly with fast page load speed
Ability to edit after ourselves in Wordpress
Attractive home page with logo etc.
Logo colours are: for the blue the pantone color is #0355a3
and for the green is #8cc63f

Sections, about us, what we do/services we provide, contact us

```html
<!DOCTYPE html>
<html lang="en">
<head>
<meta charset="utf-8">
<title>Vel-Cora Solutions</title>
<link href="https://fonts.googleapis.com/css2?family=Lato:wght@400;700;900&display=swap" rel="stylesheet">
<style>
:root{
  --blue:#0b3f93;
  --blue-deep:#0e4a9d;
  --green:#7fc132;
  --green-btn:#76bd2d;
  --ink:#444;
  --soft:#e9eef7;
  --white:#fff;
}
*{margin:0;padding:0;box-sizing:border-box}
html,body{width:1200px;height:3627px;overflow:hidden}
body{position:relative;font-family:'Lato',sans-serif;color:var(--ink);background:var(--white)}
.abs{position:absolute}
section,header,footer{position:absolute;left:0;width:1200px}

/* header */
.site-header{top:0;height:108px;background:var(--white)}
.brand{left:77px;top:26px;display:flex;align-items:center;gap:12px}
.brand-mark{width:54px;height:54px;background:var(--blue)}
.brand-name{color:var(--blue);font-weight:900;font-size:25px;line-height:26px;letter-spacing:.5px}
.main-nav{left:415px;top:44px;display:flex;font-size:17px;font-weight:700;color:#333}
.main-nav span{padding:0 22px;border-left:1px solid #bbb;line-height:20px}
.main-nav span:first-child{border-left:none;padding-left:0;color:var(--blue)}
.nav-tick{left:453px;top:16px}

/* hero */
.hero{top:108px;height:586px;overflow:hidden}
.hero-photo{position:absolute;inset:0;background:linear-gradient(100deg,#1f2a4d 0%,#3a4c86 40%,#6a5c7a 65%,#c8602a 88%,#e27a1c 100%)}
.hero-badge{left:88px;top:81px;width:402px;height:402px;border-radius:50%;background:linear-gradient(150deg,#5a9a3a 0%,#3f8a58 45%,#2a6f8c 100%);text-align:center;color:var(--white)}
.hero-ring{left:100px;top:76px;width:400px;height:408px;border-radius:50%;border:3px solid rgba(255,255,255,.85);border-left-color:transparent;border-top-color:transparent}
.hero-welcome{position:absolute;top:101px;width:100%;font-size:27px;letter-spacing:1px}
.hero-title{position:absolute;top:140px;width:100%;font-size:50px;font-weight:900;line-height:48px}
.hero-btn{position:absolute;left:111px;top:259px;width:174px;height:53px;border:2px solid var(--white);border-radius:27px;font-size:17px;line-height:49px;font-weight:700}
.hero-arrow{top:258px}

/* about */
.about{top:694px;height:527px;background:var(--soft)}
.about-media{left:159px;top:73px;width:369px;height:345px;background:linear-gradient(135deg,#c7d2e2,#8aa0bb 55%,#5b6f86)}
.section-title{font-weight:900;color:var(--blue);text-align:center;letter-spacing:-.5px}
.rule{height:3px;width:44px;background:var(--blue);margin:8px auto 0}
.about-title{left:560px;top:93px;width:446px;font-size:35px}
.about-copy{left:560px;top:168px;width:446px;text-align:center;font-size:15.5px;line-height:27px;color:#444}
.about-copy p+p{margin-top:11px}
.btn-green{background:var(--green-btn);color:var(--white);font-weight:700;text-align:center;border-radius:28px}
.about-btn{left:701px;top:365px;width:183px;height:56px;line-height:56px;font-size:17px}

/* services */
.services{top:1221px;height:628px;background:var(--white)}
.services-title{left:0;top:60px;width:1200px;font-size:35px}
.service{width:485px;height:171px;border:3px solid var(--green);border-radius:85px;padding:34px 38px}
.service h3{font-size:20px;font-weight:900;color:var(--blue);margin-bottom:8px}
.service p{font-size:14px;line-height:23px;color:#555}
.service.left{text-align:right;padding-right:100px}
.service.right{padding-left:108px}
.service svg{position:absolute;top:52px}
.service.left svg{right:22px}
.service.right svg{left:30px}
.hub{left:549px;top:1515px;width:96px;height:96px;border-radius:50%;background:var(--white);border:3px solid #e3e8ee;display:flex;align-items:center;justify-content:center}
.hub-dot{width:40px;height:40px;border-radius:50%;background:var(--blue)}

/* blogs */
.blogs{top:1849px;height:569px;background:var(--green)}
.blogs-title{top:50px;width:1200px;text-align:center;color:var(--white);font-size:33px;font-weight:900}
.blogs-title .rule{background:var(--white)}
.post{top:131px;width:310px;height:373px;background:var(--white);text-align:center}
.post-media{height:197px}
.post-date{margin-top:22px;font-size:15px;font-weight:900;color:var(--blue)}
.post-title{margin-top:6px;font-size:19px;line-height:24px;color:#444;padding:0 20px}
.post-btn{display:block;margin:18px auto 0;width:138px;height:44px;line-height:44px;border-radius:22px;background:var(--blue);color:var(--white);font-size:13px;font-weight:700}

/* partners */
.partners{top:2418px;height:466px;background:linear-gradient(180deg,#f3f4f6,#e6e8ec)}
.partners-title{top:62px;width:1200px;text-align:center;font-size:33px;font-weight:900;color:#222}
.partners-title .rule{background:var(--green)}
.partner{top:153px;width:414px;height:214px;background:var(--white);border:2px solid #d9dbe0;text-align:center}
.partner-name{margin-top:54px;font-size:32px;font-weight:900;color:#222;letter-spacing:1px}
.partner-role{margin-top:26px;font-size:18px;font-weight:700;color:#777}

/* contact */
.contact{top:2884px;height:558px;background:var(--blue-deep);color:var(--white)}
.contact-title{left:148px;top:90px;font-size:32px;font-weight:900}
.contact-title .rule{background:var(--white);margin:4px 0 0;width:58px}
.info{left:141px;display:flex;gap:18px}
.info-icon{width:76px;height:76px;border-radius:50%;border:2px solid var(--white);display:flex;align-items:center;justify-content:center;flex:none}
.info h4{font-size:20px;font-weight:700;margin-top:-6px}
.info p{font-size:20px;line-height:31px}
.field{background:var(--white);color:#333;font-size:12px;padding:14px 18px;height:48px}
.submit{left:521px;top:391px;width:173px;height:49px;line-height:49px;font-size:19px;border-radius:25px}

/* footer */
.site-footer{top:3442px;height:185px;background:var(--white);text-align:center}
.social{top:31px;left:500px;display:flex;gap:7px}
.social-link{width:43px;height:43px;border-radius:50%;border:2px solid var(--green);display:flex;align-items:center;justify-content:center}
.foot-nav{top:88px;left:0;width:1200px;display:flex;justify-content:center;gap:49px;font-size:17px;font-weight:700;color:#333}
.copyright{top:126px;width:1200px;font-size:13px;color:#444}
</style>
</head>
<body>

<header class="site-header">
  <div class="abs brand"><span class="brand-mark"></span><span class="brand-name">VEL-CORA<br>SOLUTIONS</span></div>
  <svg class="abs nav-tick" width="32" height="24" viewBox="0 0 32 24"><path d="M3 12l9 9L29 3" fill="none" stroke="var(--green)" stroke-width="4"/></svg>
  <nav class="abs main-nav"><span>ABOUT US</span><span>OUR WORK</span><span>OUR PARTNERS</span><span>LATEST NEWS</span><span>CONTACT</span></nav>
</header>

<section class="hero">
  <div class="hero-photo" role="img" aria-label="Construction cranes over a city skyline at sunset with a rising market chart"></div>
  <div class="abs hero-ring"></div>
  <div class="abs hero-badge">
    <div class="hero-welcome">WELCOME TO</div>
    <div class="hero-title">VEL-CORA<br>SOLUTIONS</div>
    <div class="hero-btn">LEARN MORE</div>
  </div>
  <svg class="abs hero-arrow" style="left:34px" width="24" height="44" viewBox="0 0 24 44"><path d="M20 4L4 22l16 18" fill="none" stroke="#fff" stroke-width="4"/></svg>
  <svg class="abs hero-arrow" style="left:1138px" width="24" height="44" viewBox="0 0 24 44"><path d="M4 4l16 18L4 40" fill="none" stroke="#fff" stroke-width="4"/></svg>
</section>

<section class="about">
  <div class="abs about-media" role="img" aria-label="Stethoscope over financial charts in a medical theme"></div>
  <h2 class="abs section-title about-title">ABOUT VEL-CORA<div class="rule"></div></h2>
  <div class="abs about-copy">
    <p>Vel Cora is an investment company put together by a group of seasoned business professionals who have come together to combine decades of success in the real estate development, management, financing and medical services.</p>
    <p>The company will be a full service company offering turn key solutions for medical professionals.</p>
  </div>
  <div class="abs btn-green about-btn">LEARN MORE</div>
</section>

<section class="services">
  <h2 class="abs section-title services-title">WHAT WE DO<div class="rule" style="background:#222"></div></h2>
</section>
<div class="abs service left" style="left:101px;top:1383px">
  <h3>REALESTATE DEVELOPMENT</h3>
  <p>Pellentesque nibh libero ultricies eu sagittis non mollis sed justo Praesent metus ipsum pulvinar pulvinar porta id fringilla at est Phasellus felis dolor</p>
  <svg width="64" height="64" viewBox="0 0 64 64" fill="none" stroke="var(--green)" stroke-width="2"><rect x="24" y="4" width="22" height="40"/><rect x="12" y="20" width="14" height="24"/><path d="M29 10h4M37 10h4M29 18h4M37 18h4M29 26h4M37 26h4M29 34h4M37 34h4M16 28h6M16 36h6M4 50h22l14 6 20-10"/></svg>
</div>
<div class="abs service right" style="left:607px;top:1383px">
  <h3>REALESTATE MANAGEMENT</h3>
  <p>Pellentesque nibh libero ultricies eu sagittis non mollis sed justo Praesent metus ipsum pulvinar pulvinar porta id fringilla at est Phasellus felis dolor</p>
  <svg width="60" height="64" viewBox="0 0 60 64" fill="none" stroke="var(--green)" stroke-width="2"><path d="M4 6h50M4 6l4 4M18 58V44c-8-4-10-14-6-22 4-8 14-10 22-6 8 4 10 12 8 18l4 8h-6v8H30v8"/><circle cx="30" cy="30" r="6"/></svg>
</div>
<div class="abs service left" style="left:101px;top:1571px">
  <h3>FINANCING</h3>
  <p>Pellentesque nibh libero ultricies eu sagittis non mollis sed justo Praesent metus ipsum pulvinar pulvinar porta id fringilla at est Phasellus felis dolor</p>
  <svg width="64" height="64" viewBox="0 0 64 64" fill="none" stroke="var(--green)" stroke-width="2"><rect x="6" y="46" width="8" height="12"/><rect x="18" y="40" width="8" height="18"/><rect x="30" y="32" width="8" height="26"/><rect x="42" y="22" width="8" height="36"/><path d="M6 34L46 6M38 6h8v8"/></svg>
</div>
<div class="abs service right" style="left:607px;top:1571px">
  <h3>MEDICAL SERVICES</h3>
  <p>Pellentesque nibh libero ultricies eu sagittis non mollis sed justo Praesent metus ipsum pulvinar pulvinar porta id fringilla at est Phasellus felis dolor</p>
  <svg width="60" height="64" viewBox="0 0 60 64" fill="none" stroke="var(--green)" stroke-width="2"><rect x="18" y="4" width="24" height="56"/><rect x="4" y="24" width="14" height="36"/><rect x="42" y="24" width="14" height="36"/><path d="M30 10v12M24 16h12M8 32h6M8 42h6M8 52h6M46 32h6M46 42h6M46 52h6M26 48h8v12h-8z"/></svg>
</div>
<div class="abs hub"><span class="hub-dot"></span></div>

<section class="blogs">
  <h2 class="abs blogs-title">LATEST BLOGS<div class="rule"></div></h2>
  <article class="abs post" style="left:114px">
    <div class="post-media" role="img" aria-label="Model house beside stacks of coins with a crane at sunrise" style="background:linear-gradient(135deg,#c9c4bb,#d9a25a 60%,#8d6a3a)"></div>
    <div class="post-date">&#9636; 25 MAR 2020</div>
    <div class="post-title">Fusce tellus Sed metus augue convallis et vehicula</div>
    <span class="post-btn">LEARN MORE</span>
  </article>
  <article class="abs post" style="left:442px">
    <div class="post-media" role="img" aria-label="Business team reviewing documents around a laptop in an office" style="background:linear-gradient(135deg,#e6e9ee,#b7bfca 60%,#5f6b7c)"></div>
    <div class="post-date">&#9636; 15 MAR 2020</div>
    <div class="post-title">Fusce tellus Sed metus augue convallis et vehicula</div>
    <span class="post-btn">LEARN MORE</span>
  </article>
  <article class="abs post" style="left:773px">
    <div class="post-media" role="img" aria-label="Commercial building with trees under a blue sky" style="background:linear-gradient(180deg,#4d78b8 0%,#9ab2d6 35%,#d8d8d4 36%,#c9c9c3 80%,#6f7d5a 100%)"></div>
    <div class="post-date">&#9636; 02 MAR 2020</div>
    <div class="post-title">Fusce tellus Sed metus augue convallis et vehicula</div>
    <span class="post-btn">LEARN MORE</span>
  </article>
</section>

<section class="partners" role="img" aria-label="Faint office building in the background">
  <h2 class="abs partners-title">OUR PARTNERS<div class="rule"></div></h2>
  <div class="abs partner" style="left:175px">
    <div class="partner-name">318 BUILDERS INC.</div>
    <div class="partner-role">CONSTRUCTION PARTNER</div>
  </div>
  <div class="abs partner" style="left:613px">
    <div class="partner-name">NORVIXA</div>
    <div class="partner-role">EQUIPMENT LEASING PARTNER</div>
  </div>
</section>

<section class="contact">
  <h2 class="abs contact-title">CONTACT US<div class="rule"></div></h2>
  <div class="abs info" style="top:172px">
    <div class="info-icon"><svg width="26" height="34" viewBox="0 0 26 34"><path d="M13 1C6 1 1 6 1 13c0 9 12 20 12 20s12-11 12-20C25 6 20 1 13 1z" fill="#fff"/><circle cx="13" cy="13" r="5" fill="var(--blue-deep)"/></svg></div>
    <div><h4>Address</h4><p>482 Larkmoor Avenue #7<br>Texas 10931 TX</p></div>
  </div>
  <div class="abs info" style="top:286px">
    <div class="info-icon"><svg width="28" height="28" viewBox="0 0 24 24"><path d="M6.6 10.8a15 15 0 006.6 6.6l2.2-2.2c.3-.3.7-.4 1-.2 1.1.4 2.3.6 3.6.6.6 0 1 .4 1 1V20c0 .6-.4 1-1 1A17 17 0 013 4c0-.6.4-1 1-1h3.5c.6 0 1 .4 1 1 0 1.3.2 2.5.6 3.6.1.3 0 .7-.2 1z" fill="#fff"/></svg></div>
    <div><h4>Phone Number</h4><p>(555) 014 3870</p></div>
  </div>
  <div class="abs info" style="top:386px">
    <div class="info-icon"><svg width="28" height="22" viewBox="0 0 28 22"><rect x="1" y="1" width="26" height="20" rx="2" fill="#fff"/><path d="M2 3l12 9 12-9" fill="none" stroke="var(--blue-deep)" stroke-width="2"/></svg></div>
    <div><h4>Email address</h4><p>info@velcorahealth.ca</p></div>
  </div>
  <form>
    <div class="abs field" style="left:524px;top:147px;width:272px">Name:</div>
    <div class="abs field" style="left:808px;top:147px;width:272px">Phone:</div>
    <div class="abs field" style="left:524px;top:211px;width:272px">Email:</div>
    <div class="abs field" style="left:808px;top:211px;width:272px">Subject:</div>
    <div class="abs field" style="left:524px;top:274px;width:556px;height:99px">Message:</div>
    <div class="abs btn-green submit">SUBMIT</div>
  </form>
</section>

<footer class="site-footer">
  <div class="abs social">
    <span class="social-link" aria-label="Social profile 1"><svg width="20" height="20" viewBox="0 0 24 24" fill="none" stroke="var(--green)" stroke-width="2.4" stroke-linecap="round"><path d="M10 14a5 5 0 007 0l3-3a5 5 0 00-7-7l-1 1"/><path d="M14 10a5 5 0 00-7 0l-3 3a5 5 0 007 7l1-1"/></svg></span>
    <span class="social-link" aria-label="Social profile 2"><svg width="20" height="20" viewBox="0 0 24 24" fill="none" stroke="var(--green)" stroke-width="2.4" stroke-linecap="round"><path d="M10 14a5 5 0 007 0l3-3a5 5 0 00-7-7l-1 1"/><path d="M14 10a5 5 0 00-7 0l-3 3a5 5 0 007 7l1-1"/></svg></span>
    <span class="social-link" aria-label="Social profile 3"><svg width="20" height="20" viewBox="0 0 24 24" fill="none" stroke="var(--green)" stroke-width="2.4" stroke-linecap="round"><path d="M10 14a5 5 0 007 0l3-3a5 5 0 00-7-7l-1 1"/><path d="M14 10a5 5 0 00-7 0l-3 3a5 5 0 007 7l1-1"/></svg></span>
    <span class="social-link" aria-label="Social profile 4"><svg width="20" height="20" viewBox="0 0 24 24" fill="none" stroke="var(--green)" stroke-width="2.4" stroke-linecap="round"><path d="M10 14a5 5 0 007 0l3-3a5 5 0 00-7-7l-1 1"/><path d="M14 10a5 5 0 00-7 0l-3 3a5 5 0 007 7l1-1"/></svg></span>
  </div>
  <nav class="abs foot-nav"><span>HOME</span><span>ABOUT US</span><span>OUR WORK</span><span>OUR PARTNERS</span><span>LATEST NEWS</span><span>CONTACT</span></nav>
  <div class="abs copyright">© 2020 Vel-Cora Solutions | All Rights Reserved | Disclaimer</div>
</footer>

</body>
</html>
```